Bright Wave Labs

We need a professional letter head format for our company. Now we have a logo but need to desing a new logo also. I have uploaded our old logo. Use the color in the logo and design a new one.

Dear Designers , Need to mention "BWL" and please dont use our old LOGO. we need a new catchy one.

```html
<!DOCTYPE html>
<html lang="en">
<head>
<meta charset="UTF-8">
<title>Bright Wave Labs — Letterhead</title>
<link href="https://fonts.googleapis.com/css2?family=Source+Sans+3:wght@400;600;700&family=Arimo:wght@700&display=swap" rel="stylesheet">
<style>
  :root {
    --backdrop: #e9eaec;
    --paper: #ffffff;
    --lime: #94c43d;
    --navy: #0f2239;
    --ink: #2f2f33;
    --ink-strong: #111111;
  }
  * { margin: 0; padding: 0; box-sizing: border-box; }
  html, body { width: 1200px; height: 1200px; overflow: hidden; }
  body {
    background: var(--backdrop);
    font-family: "Source Sans 3", sans-serif;
    color: var(--ink);
  }
  .letterhead {
    position: absolute;
    left: 250px; top: 67px;
    width: 740px; height: 1043px;
    background: var(--paper);
    overflow: hidden;
  }
  .top-band {
    position: absolute; left: 0; top: 0;
    width: 100%; height: 9px;
    background: var(--lime);
  }
  .brand {
    position: absolute; left: 0; right: 0; top: 110px;
    display: flex; align-items: center; justify-content: center; gap: 8px;
  }
  .brand-dot {
    width: 18px; height: 18px; border-radius: 50%;
    background: var(--lime);
  }
  .brand-name {
    font-weight: 700; font-size: 17px; letter-spacing: 0.8px;
    color: var(--navy); text-transform: uppercase;
  }
  .salutation {
    position: absolute; left: 63px; top: 249px;
    font-family: "Arimo", sans-serif; font-weight: 700;
    font-size: 15.5px; color: var(--ink-strong);
  }
  .letter-body {
    position: absolute; left: 63px; top: 290px; width: 620px;
    font-size: 14.6px; line-height: 19.4px;
    text-align: justify;
  }
  .letter-body p + p { margin-top: 19.4px; }
  .signature {
    position: absolute; left: 63px; top: 617px;
    width: 136px; height: 72px;
    background: linear-gradient(135deg, #f1f1f1, #e2e2e2);
    border-radius: 4px;
  }
  .footer-curve {
    position: absolute; left: 0; bottom: 0;
    width: 740px; height: 63px;
  }
  .contact {
    position: absolute; left: 0; right: 0; top: 982px;
    text-align: center; color: var(--ink-strong);
  }
  .contact-line {
    display: flex; justify-content: center; align-items: center; gap: 4px;
    font-size: 11.5px; line-height: 16px;
  }
  .contact-line .gap { width: 14px; }
  .contact-line svg { width: 10px; height: 10px; }
  .address { margin-top: 2px; font-size: 10.5px; line-height: 14px; letter-spacing: 0.3px; }
</style>
</head>
<body>
  <main class="letterhead">
    <div class="top-band"></div>

    <header class="brand">
      <span class="brand-dot"></span>
      <span class="brand-name">Bright Wave Labs</span>
    </header>

    <h1 class="salutation">Dear Mr. Carter,</h1>

    <section class="letter-body">
      <p>Lorem Ipsum is simply dummy text of the printing and typesetting industry. Lorem Ipsum has been the industry's standard dummy text ever since the 1500s, when an unknown printer took a galley of type and scrambled it to make a type specimen book. It has survived not only five centuries, but also the leap into electronic typesetting, remaining essentially unchanged.</p>
      <p>The standard chunk of Lorem Ipsum used since the 1500s is reproduced below for those interested. Sections 1.10.32 and 1.10.33 from "de Finibus Bonorum et Malorum" by Marcus Tellan are also reproduced in their exact original form, accompanied by English versions from the 1914 translation by H. Ardwell</p>
      <p>Lorem Ipsum is simply dummy text of the printing and typesetting industry. Lorem Ipsum has been the industry's standard dummy text ever since the 1500s, when an unknown printer took a galley of type and scrambled it to make a type specimen book. It has survived not only five centuries, but also the leap into electronic typesetting, remaining essentially unchanged. It was popularised in the</p>
    </section>

    <div class="signature" role="img" aria-label="Handwritten signature of the sender"></div>

    <svg class="footer-curve" viewBox="0 0 740 63" preserveAspectRatio="none" aria-hidden="true">
      <path d="M0,9 C250,40 500,44 740,5 C500,50 250,48 0,22 Z" fill="var(--lime)"/>
      <path d="M0,31 C250,62 500,62 740,7 L740,63 L0,63 Z" fill="var(--navy)"/>
    </svg>

    <footer class="contact">
      <div class="contact-line">
        <svg viewBox="0 0 24 24"><path fill="var(--navy)" d="M6.6 10.8a15.1 15.1 0 0 0 6.6 6.6l2.2-2.2a1 1 0 0 1 1-.25 11.4 11.4 0 0 0 3.6.57 1 1 0 0 1 1 1V20a1 1 0 0 1-1 1A17 17 0 0 1 3 4a1 1 0 0 1 1-1h3.5a1 1 0 0 1 1 1c0 1.25.2 2.45.57 3.57a1 1 0 0 1-.25 1z"/></svg>
        <span>(+820)414-337-219</span>
        <svg viewBox="0 0 24 24"><path fill="none" stroke="var(--navy)" stroke-width="2.5" d="M3 6h18v12H3z M3 6l9 7 9-7"/></svg>
        <span>info@brightwavelabs.com</span>
        <span class="gap"></span>
        <span>www.brightwavelabs.com</span>
      </div>
      <div class="address">Po. box 201, Street Name, City Name, Zip Code - 00000</div>
    </footer>
  </main>
</body>
</html>
```